Brellwick Partners, LLC Stationary

Brellwick Partners, LLC is a new financial planning and consulting company. We are looking for designs on business cards, letterhead, envelopes, and anything else that would be useful. Our preference for business card design is two sided. We are looking for a professional and clean look with incorporating the logo and patriotic feel. Thank you to all who participate and good luck!

```html
<!DOCTYPE html>
<html lang="en">
<head>
<meta charset="utf-8">
<title>Brellwick Partners, LLC — Business Card</title>
<link href="https://fonts.googleapis.com/css2?family=Open+Sans:wght@400;600&display=swap" rel="stylesheet">
<style>
  :root {
    --navy: #0b3a6e;
    --navy-deep: #082f5c;
    --red: #d10f1a;
    --white: #ffffff;
    --ink: #333a44;
    --muted: #9aa0a8;
    --backdrop: #e4e5e8;
  }
  * { box-sizing: border-box; margin: 0; padding: 0; }
  html, body { width: 1200px; height: 800px; overflow: hidden; }
  body {
    background: var(--backdrop);
    font-family: "Open Sans", sans-serif;
    position: relative;
  }
  .card {
    position: absolute;
    top: 252px;
    width: 520px;
    height: 297px;
    border-radius: 3px;
    overflow: hidden;
    box-shadow: 0 10px 24px rgba(0,0,0,0.14);
  }
  /* Front */
  .card-front {
    left: 50px;
    background: linear-gradient(135deg, #123f78 0%, var(--navy-deep) 60%, #0d3a6c 100%);
    display: flex;
    align-items: center;
    justify-content: center;
  }
  .brand-front {
    display: flex;
    align-items: center;
    gap: 14px;
    color: var(--white);
    font-weight: 600;
    font-size: 26px;
    letter-spacing: 0.04em;
    text-transform: uppercase;
  }
  .brand-mark {
    width: 16px;
    height: 16px;
    background: var(--white);
    flex: none;
  }
  /* Back */
  .card-back {
    left: 630px;
    background: var(--white);
  }
  .band-top {
    position: absolute; left: 0; top: 0; width: 100%; height: 20px;
    background: var(--navy);
  }
  .band-bottom {
    position: absolute; left: 0; bottom: 0; width: 100%; height: 24px;
    background: var(--red);
  }
  .brand-back {
    position: absolute;
    left: 30px;
    top: 46px;
    display: flex;
    align-items: center;
    gap: 10px;
    color: var(--navy);
    font-weight: 600;
    font-size: 18px;
    letter-spacing: 0.04em;
    text-transform: uppercase;
  }
  .brand-back .brand-mark { width: 12px; height: 12px; background: var(--navy); }
  .address {
    position: absolute;
    left: 30px;
    top: 96px;
    font-size: 12px;
    line-height: 1.4;
    color: var(--ink);
  }
  .contact-list {
    position: absolute;
    left: 30px;
    top: 140px;
    list-style: none;
  }
  .contact-list li {
    display: flex;
    align-items: center;
    gap: 10px;
    font-size: 12px;
    color: var(--ink);
    height: 24px;
  }
  .contact-icon {
    width: 20px; height: 20px;
    border-radius: 4px;
    background: var(--navy);
    display: flex; align-items: center; justify-content: center;
    flex: none;
  }
  .signature {
    position: absolute;
    right: 32px;
    bottom: 48px;
    text-align: left;
  }
  .person-name {
    color: var(--navy);
    font-size: 17px;
    font-weight: 400;
  }
  .person-role {
    color: var(--muted);
    font-size: 12px;
  }
</style>
</head>
<body>
  <section class="card card-front" aria-label="Card front">
    <div class="brand-front">
      <span class="brand-mark"></span>
      <span class="brand-name">Brellwick Partners, LLC</span>
    </div>
  </section>

  <section class="card card-back" aria-label="Card back">
    <div class="band-top"></div>
    <div class="brand-back">
      <span class="brand-mark"></span>
      <span class="brand-name">Brellwick Partners, LLC</span>
    </div>
    <p class="address">418 Alder Crest Ave # 210, Fairbrook,<br>GA 30999, USA</p>
    <ul class="contact-list">
      <li>
        <span class="contact-icon">
          <svg width="12" height="12" viewBox="0 0 24 24" fill="#fff"><path d="M6.6 10.8a15 15 0 0 0 6.6 6.6l2.2-2.2a1 1 0 0 1 1-.25 11.4 11.4 0 0 0 3.6.57 1 1 0 0 1 1 1V20a1 1 0 0 1-1 1A17 17 0 0 1 3 4a1 1 0 0 1 1-1h3.5a1 1 0 0 1 1 1c0 1.25.2 2.45.57 3.57a1 1 0 0 1-.25 1z"/></svg>
        </span>
        <span>+1 555-014-2290</span>
      </li>
      <li>
        <span class="contact-icon">
          <svg width="12" height="12" viewBox="0 0 24 24" fill="none" stroke="#fff" stroke-width="2"><rect x="3" y="5" width="18" height="14" rx="1"/><path d="M3 6l9 7 9-7"/></svg>
        </span>
        <span>info@BrellwickPartners.com</span>
      </li>
      <li>
        <span class="contact-icon">
          <svg width="12" height="12" viewBox="0 0 24 24" fill="none" stroke="#fff" stroke-width="2"><circle cx="12" cy="12" r="9"/><path d="M3 12h18M12 3c3 3 3 15 0 18M12 3c-3 3-3 15 0 18"/></svg>
        </span>
        <span>www.BrellwickPartners.com</span>
      </li>
    </ul>
    <div class="signature">
      <p class="person-name">Daniel Hartley</p>
      <p class="person-role">Financial Advisor</p>
    </div>
    <div class="band-bottom"></div>
  </section>
</body>
</html>
```